Duct Manufacturing Company new to the industry needs business card and stationary design

we are sheet metal duct manufacturers looking for a business card design to fit my new business logo.
nothing to crazy that will date, but want it to stand out from the crowed.
I'm sure you guys will work it out.

Contact Information for Business Card

Glen Marsh
Director

Address
17 Dorwell St
Carrowie NSW 2641

0438 760 514

Sales@flowbend.com.au

Font styles to use
Other font styles liked:
• BankGothic md bt

Requirements
Nice to have
• Like the idea of corner rounded to match logo
• like to keep colours flowing
• font I like sharp square not rounded

```html
<!DOCTYPE html>
<html lang="en">
<head>
<meta charset="utf-8">
<title>Flowbend Industries — Business Card</title>
<link href="https://fonts.googleapis.com/css2?family=Open+Sans:wght@400;600;700&display=swap" rel="stylesheet">
<style>
  :root {
    --backdrop: #3a3a3a;
    --metal-light: #e9eaeb;
    --metal-mid: #c9cacc;
    --metal-dark: #9d9fa2;
    --ink: #1d1f22;
    --brand-blue: #0f4f9c;
    --accent-blue: #1a6fd1;
    --brand-green: #5a9e2f;
  }
  * { margin: 0; padding: 0; box-sizing: border-box; }
  html, body {
    width: 1200px;
    height: 750px;
    overflow: hidden;
    background: var(--backdrop);
    font-family: "Open Sans", Arial, sans-serif;
  }
  .business-card {
    position: absolute;
    left: 370px;
    top: 244px;
    width: 460px;
    height: 262px;
    overflow: hidden;
    background:
      repeating-linear-gradient(90deg, rgba(0,0,0,0.04) 0 1px, rgba(255,255,255,0.05) 1px 3px),
      linear-gradient(180deg, rgba(255,255,255,0) 0%, rgba(255,255,255,0.35) 45%, rgba(255,255,255,0) 100%),
      linear-gradient(90deg, var(--metal-dark) 0%, var(--metal-light) 28%, var(--metal-mid) 55%, var(--metal-light) 78%, var(--metal-dark) 100%);
  }
  .brand {
    position: absolute;
    left: 30px;
    top: 32px;
    width: 150px;
    text-align center;
    text-align: center;
  }
  .brand-dot {
    display: block;
    width: 44px;
    height: 44px;
    margin: 0 auto 12px;
    border-radius: 50%;
    background: var(--brand-green);
  }
  .brand-name {
    color: var(--brand-green);
    font-weight: 700;
    font-size: 17px;
    line-height: 1.15;
    letter-spacing: 0.5px;
  }
  .address {
    position: absolute;
    left: 29px;
    top: 152px;
    color: var(--ink);
    font-size: 11px;
    line-height: 14px;
  }
  .contact-list {
    position: absolute;
    left: 29px;
    top: 192px;
    list-style: none;
    color: var(--ink);
    font-size: 11px;
  }
  .contact-list li {
    display: flex;
    align-items: center;
    height: 17.5px;
  }
  .contact-list svg {
    width: 12px;
    height: 12px;
    margin-right: 6px;
    fill: var(--brand-blue);
    flex: none;
  }
  .person {
    position: absolute;
    right: 28px;
    top: 176px;
    text-align: right;
  }
  .person-name {
    color: var(--brand-blue);
    font-weight: 600;
    font-size: 19px;
    line-height: 22px;
  }
  .person-title {
    color: var(--ink);
    font-size: 14px;
    line-height: 18px;
  }
  .accent-bar {
    position: absolute;
    right: 0;
    top: 180px;
    width: 9px;
    height: 38px;
    background: var(--accent-blue);
  }
</style>
</head>
<body>
  <div class="business-card">
    <div class="brand">
      <span class="brand-dot"></span>
      <div class="brand-name">FLOWBEND<br>INDUSTRIES</div>
    </div>

    <p class="address">17 Dorwell St<br>Carrowie NSW 2641</p>

    <ul class="contact-list">
      <li>
        <svg viewBox="0 0 24 24" aria-hidden="true"><path d="M6.6 10.8a15.2 15.2 0 0 0 6.6 6.6l2.2-2.2a1 1 0 0 1 1-.25 11.4 11.4 0 0 0 3.6.57 1 1 0 0 1 1 1V20a1 1 0 0 1-1 1A17 17 0 0 1 3 4a1 1 0 0 1 1-1h3.5a1 1 0 0 1 1 1c0 1.25.2 2.45.57 3.6a1 1 0 0 1-.25 1z"/></svg>
        0438 760 514
      </li>
      <li>
        <svg viewBox="0 0 24 24" aria-hidden="true"><path d="M2 5h20v14H2z M3.5 6.5 12 12.5l8.5-6" stroke="#fff" stroke-width="1.5"/></svg>
        Sales@flowbend.com.au
      </li>
      <li>
        <svg viewBox="0 0 24 24" aria-hidden="true"><circle cx="12" cy="12" r="10"/><path d="M2 12h20M12 2c3 3 3 17 0 20M12 2c-3 3-3 17 0 20" stroke="#fff" stroke-width="1.3" fill="none"/></svg>
        www.flowbend.com.au
      </li>
    </ul>

    <div class="person">
      <div class="person-name">Glen Marsh</div>
      <div class="person-title">Director</div>
    </div>
    <div class="accent-bar"></div>
  </div>
</body>
</html>
```